WEBSITE & LOGO for MEDICAL CILINC

BRAND NAME ( LUMORA) Medical clinic for intravenous (IV) vitamin hydration and wellness therapy. range of signature infusions and boosters are targeted at preventative health and wellness – essentially replenishing your body with the fluids and vitamins it needs to be in tip-top condition.

Blood testing
laboratory analysis
IV therapy
IV infusion drips
phlebotomy services
nurses for Home care services
Patient repatriation services to their countries
Hire of medical equipments including beds and wheel chairs

www.quellsa.com
www.tovexclinic.com
http://pickaflask.co.uk

All adults
18+ women and men.

No black color in the background
DNA double helix image should to be implemented in the design and logo.
the website should be easy to be used so the clients can add to the shopping cart
- select treatment or drips
- supplement
- book nurses
- book home visit
- book nurse for international home care journey

Colors
86cae7
33b8a4
e4daeb
f9d9e8
fefafc
fbd2d3
eee9f4
85acd3
0455a3

Requirements
Must have
• DNA Double helix in Java animation
injection icon for IV injection
Infusion Icon Bag for IV infusion
Analysis icon
phlebotomy services icon
Patient repatriation services icon
Hire of medical equipments icon

light background and water blue menu and buttons with highlights
Nice to have
• dynamic website where
IV injections scroll from side to side
IV infusion scroll from side to side.

```html
<!DOCTYPE html>
<html lang="en">
<head>
<meta charset="utf-8">
<title>Lumora — IV Vitamin Hydration & Wellness Clinic</title>
<link href="https://fonts.googleapis.com/css2?family=Michroma&family=Jost:wght@400;500&family=Arimo:wght@400;700&display=swap" rel="stylesheet">
<style>
:root{
  --navy:#0455a3;
  --sky:#86cae7;
  --teal:#33b8a4;
  --lilac:#e4daeb;
  --pink:#f4c3da;
  --blush:#fefafc;
  --mist:#eee9f4;
  --steel:#85acd3;
  --ink:#1b1b22;
  --body:#3a3a44;
  --white:#ffffff;
}
*{margin:0;padding:0;box-sizing:border-box}
html,body{width:1200px;height:3334px;overflow:hidden}
body{position:relative;background:var(--white);font-family:"Arimo",Arial,sans-serif;color:var(--body)}
.abs{position:absolute}
.head{font-family:"Michroma","Jost",sans-serif;color:var(--ink);font-weight:400;line-height:1.3}
.head .accent{color:var(--navy)}
.btn{position:absolute;display:flex;align-items:center;justify-content:center;border-radius:26px;font-family:"Jost",sans-serif;font-size:17px;height:51px}
.btn-pink{background:var(--pink);color:#2b2b33}
.btn-blue{background:var(--navy);color:var(--white)}
.btn-ghost{border:1.5px solid var(--white);color:var(--white)}
.para{font-size:14.5px;line-height:25.5px;text-align:justify}

/* top bar */
.topbar{left:0;top:0;width:1200px;height:51px;background:var(--navy);color:var(--white);font-family:"Jost",sans-serif;font-size:14px}
.topbar .welcome{left:172px;top:16px;font-weight:500}
.topbar .account{right:173px;top:15px;display:flex;gap:9px;align-items:center}

/* header & hero */
.hero{left:0;top:51px;width:1200px;height:603px;background:linear-gradient(180deg,#fbfaff 0%,#f5f4fb 100%)}
.hero-art{left:520px;top:51px;width:680px;height:603px;background:radial-gradient(ellipse at 55% 55%,#8fb6ee 0%,#c7b4ee 30%,#f1d0e6 55%,rgba(250,246,252,0) 78%)}
.brand{left:172px;top:82px;display:flex;align-items:center;gap:12px}
.brand .dot{width:30px;height:30px;border-radius:50%;background:var(--navy)}
.brand .name{font-family:"Michroma",sans-serif;font-size:30px;color:var(--navy)}
.nav{left:572px;top:96px;display:flex;gap:0;font-family:"Jost",sans-serif;font-size:14px;color:var(--ink);text-transform:uppercase;font-weight:500}
.nav span{position:absolute;white-space:nowrap}
.hero-title{left:170px;top:274px;font-family:"Michroma",sans-serif;font-size:60px;color:var(--navy);font-weight:700;letter-spacing:1px}
.hero-text{left:172px;top:357px;font-family:"Jost",sans-serif;font-size:17px;line-height:25px;color:var(--ink)}

/* journey */
.journey-photo{left:0;top:654px;width:480px;height:444px;background:linear-gradient(90deg,#9fbde0 0%,#d6e4f3 60%,#ffffff 100%)}
.section-h{font-size:30px}

/* services */
.services{left:0;top:1098px;width:1200px;height:449px;background:#fdf6f9}
.service{position:absolute;width:200px;text-align:center}
.service .ring{width:112px;height:112px;margin:0 auto}
.service h3{font-family:"Jost",sans-serif;font-weight:400;font-size:18px;color:var(--ink);margin-top:18px}
.service p{font-size:11.5px;line-height:17px;margin-top:8px;color:#3a3a44}

/* home care */
.care-photo{left:690px;top:1547px;width:510px;height:522px;background:linear-gradient(90deg,#ffffff 0%,#b9dcd8 25%,#6fb9b4 55%,#d8d3cc 100%)}

/* preventative */
.prevent{left:0;top:2069px;width:1200px;height:477px;background:linear-gradient(180deg,#ffffff 0%,#f2f3fb 100%)}
.card{position:absolute;top:2277px;width:414px;height:175px;background:var(--white);box-shadow:0 2px 8px rgba(60,60,110,.12)}
.card .pic{position:absolute;left:9px;top:10px;width:162px;height:155px}
.card h4{position:absolute;left:185px;top:29px;font-family:"Jost",sans-serif;font-weight:400;font-size:19px;color:var(--ink)}
.card p{position:absolute;left:185px;top:62px;width:215px;font-size:11.5px;line-height:19.5px}
.card a{position:absolute;left:185px;top:127px;font-size:14px;color:var(--navy);text-decoration:none}

/* equipment band */
.band{left:0;top:2546px;width:1200px;height:451px;background:linear-gradient(135deg,#3a73c9 0%,#2d66c4 50%,#3c76cc 100%)}
.band-title{left:0;width:1200px;top:2626px;text-align:center;color:var(--white);font-size:30px;line-height:41px}
.band-text{left:195px;width:810px;top:2733px;text-align:center;color:var(--white);font-size:14.5px;line-height:25.5px}

/* footer */
.foot-h{font-family:"Jost",sans-serif;font-size:19px;color:var(--ink)}
.foot-list{font-size:13px;line-height:22.5px;color:var(--ink);list-style:none}
.input{left:786px;top:3097px;width:241px;height:42px;border:1.5px solid #9aa0b4;border-radius:21px;font-size:13px;color:var(--ink);padding:12px 12px}
.rule{left:172px;top:3268px;width:855px;height:1px;background:#b9bcc8}
.copy{left:0;width:1200px;top:3295px;text-align:center;font-size:14px;color:var(--ink)}
</style>
</head>
<body>

<!-- Top bar -->
<div class="abs topbar">
  <span class="abs welcome">Welcome To The Lumora!</span>
  <div class="abs account">
    <span>Sign Up</span><span>|</span><span>Login</span><span>|</span><span>Wishlist</span>
    <svg width="22" height="24" viewBox="0 0 22 24" style="margin-left:14px"><path d="M3 7h16l-1 15H4z" fill="none" stroke="#fff" stroke-width="1.6"/><path d="M7 10V5a4 4 0 0 1 8 0v5" fill="none" stroke="#fff" stroke-width="1.6"/></svg>
    <span>Cart: 0Items</span>
  </div>
</div>

<!-- Hero -->
<div class="abs hero"></div>
<div class="abs hero-art" role="img" aria-label="Glossy blue and pink DNA double helix spiralling across the hero"></div>
<div class="abs brand"><span class="dot"></span><span class="name">Lumora</span></div>
<nav class="abs nav">
  <span style="left:0;text-decoration:underline">Home</span>
  <span style="left:66px">About</span>
  <span style="left:136px">Products</span>
  <span style="left:234px">Services</span>
  <span style="left:324px">Blog</span>
  <span style="left:391px">Contact</span>
</nav>
<h1 class="abs hero-title">Lumora</h1>
<p class="abs hero-text">We are a medical clinic for intravenous (IV)<br>vitamin hydration and wellness therapy.</p>
<div class="btn btn-pink" style="left:172px;top:430px;width:120px">Read More</div>

<!-- International journey -->
<div class="abs journey-photo" role="img" aria-label="Lab scientist in mask and goggles examining a test tube"></div>
<h2 class="abs head section-h" style="left:503px;top:722px">Nurse For International Home<br><span class="accent">Care Journey</span></h2>
<p class="abs para" style="left:505px;top:829px;width:521px">We are a medical clinic for intravenous (IV) vitamin hydration and wellness therapy. A range of signature infusions and boosters are targeted at preventative health and wellness – essentially replenishing your body with the fluids and vitamins it needs to be in tip-top condition.</p>
<div class="btn btn-pink" style="left:505px;top:960px;width:121px">Read More</div>

<!-- Services -->
<div class="abs services"></div>
<h2 class="abs head section-h" style="left:0;width:1200px;text-align:center;top:1163px">Our <span class="accent">Services</span></h2>

<svg class="abs" style="left:66px;top:1352px" width="28" height="46" viewBox="0 0 28 46"><path d="M24 3L4 23l20 20" fill="none" stroke="#444" stroke-width="2"/></svg>
<svg class="abs" style="left:1100px;top:1352px" width="28" height="46" viewBox="0 0 28 46"><path d="M4 3l20 20L4 43" fill="none" stroke="#444" stroke-width="2"/></svg>

<div class="service" style="left:152px;top:1251px">
  <svg class="ring" viewBox="0 0 112 112"><circle cx="56" cy="56" r="52" fill="#fff" stroke="#86cae7" stroke-width="3" stroke-dasharray="4 5"/><circle cx="56" cy="56" r="52" fill="none" stroke="#e58cc0" stroke-width="3" stroke-dasharray="3 6" stroke-dashoffset="4"/>
    <g transform="rotate(-30 56 56)"><rect x="34" y="48" width="44" height="16" rx="8" fill="none" stroke="#1b2a4a" stroke-width="2.5"/><rect x="36" y="50" width="22" height="12" rx="6" fill="#0455a3"/></g><circle cx="74" cy="70" r="3" fill="#0455a3"/></svg>
  <h3>Blood Testing</h3>
  <p>Duis aute irure dolor in<br>reprehenderit in voluptate velit<br>esse cillum dolorem.</p>
</div>
<div class="service" style="left:390px;top:1251px">
  <svg class="ring" viewBox="0 0 112 112"><circle cx="56" cy="56" r="52" fill="#fff" stroke="#86cae7" stroke-width="3" stroke-dasharray="4 5"/><circle cx="56" cy="56" r="52" fill="none" stroke="#e58cc0" stroke-width="3" stroke-dasharray="3 6" stroke-dashoffset="4"/>
    <path d="M50 34h12M52 34v16L40 74h32L60 50V34" fill="none" stroke="#1b2a4a" stroke-width="2.5" stroke-linejoin="round"/><path d="M45 64h22l5 10H40z" fill="#0455a3"/></svg>
  <h3>Laboratory Analysis</h3>
  <p>Duis aute irure dolor in<br>reprehenderit in voluptate velit<br>esse cillum dolorem.</p>
</div>
<div class="service" style="left:618px;top:1251px">
  <svg class="ring" viewBox="0 0 112 112"><circle cx="56" cy="56" r="52" fill="#fff" stroke="#86cae7" stroke-width="3" stroke-dasharray="4 5"/><circle cx="56" cy="56" r="52" fill="none" stroke="#e58cc0" stroke-width="3" stroke-dasharray="3 6" stroke-dashoffset="4"/>
    <g transform="rotate(-45 56 56)"><rect x="32" y="50" width="40" height="12" fill="none" stroke="#1b2a4a" stroke-width="2.5"/><rect x="34" y="52" width="22" height="8" fill="#0455a3"/><path d="M72 56h16M26 48v16M26 56h6" stroke="#1b2a4a" stroke-width="2.5"/></g></svg>
  <h3>IV Therapy</h3>
  <p>Duis aute irure dolor in<br>reprehenderit in voluptate velit<br>esse cillum dolorem.</p>
</div>
<div class="service" style="left:844px;top:1251px">
  <svg class="ring" viewBox="0 0 112 112"><circle cx="56" cy="56" r="52" fill="#fff" stroke="#86cae7" stroke-width="3" stroke-dasharray="4 5"/><circle cx="56" cy="56" r="52" fill="none" stroke="#e58cc0" stroke-width="3" stroke-dasharray="3 6" stroke-dashoffset="4"/>
    <path d="M48 36h18l8 8v30H48z" fill="#fff" stroke="#1b2a4a" stroke-width="2.5"/><path d="M56 48h12M56 55h12M56 62h12" stroke="#1b2a4a" stroke-width="2"/><circle cx="46" cy="62" r="8" fill="#fff" stroke="#0455a3" stroke-width="2.5"/><path d="M40 68l-6 6" stroke="#0455a3" stroke-width="3"/></svg>
  <h3>IV Infusion Drips</h3>
  <p>Duis aute irure dolor in<br>reprehenderit in voluptate velit<br>esse cillum dolorem.</p>
</div>

<!-- Home care -->
<div class="abs care-photo" role="img" aria-label="Nurse in teal scrubs taking notes beside a smiling senior patient"></div>
<h2 class="abs head section-h" style="left:172px;top:1662px">Nurse For<br><span class="accent">Home care services</span></h2>
<p class="abs para" style="left:173px;top:1759px;width:521px">We are a medical clinic for intravenous (IV) vitamin hydration and wellness therapy. A range of signature infusions and boosters are targeted at preventative health and wellness – essentially replenishing your body with the fluids and vitamins it needs to be in tip-top condition.</p>
<div class="btn btn-pink" style="left:174px;top:1897px;width:120px">Book Nurses</div>
<div class="btn btn-blue" style="left:302px;top:1897px;width:157px">Book Home Visit</div>

<!-- Preventative -->
<div class="abs prevent"></div>
<h2 class="abs head section-h" style="left:0;width:1200px;text-align:center;top:2146px">Preventative Health And<br><span class="accent">Wellness</span></h2>
<div class="card" style="left:172px">
  <div class="pic" role="img" aria-label="Blood testing laboratory equipment" style="background:linear-gradient(135deg,#6f8fb6 0%,#c9d6e6 50%,#e9a48c 100%)"></div>
  <h4>Phlebotomy Services</h4>
  <p>Duis aute irure dolor in reprehenderit in voluptate velit esse cillum dolorem. Duis aute irure dolor.</p>
  <a>Read More &gt;&gt;</a>
</div>
<div class="card" style="left:614px">
  <div class="pic" role="img" aria-label="Doctor in a white coat in a clinical lab" style="background:linear-gradient(135deg,#cfd8e2 0%,#eef1f5 50%,#8fa1b6 100%)"></div>
  <h4>Patient Repatriation</h4>
  <p>Duis aute irure dolor in reprehenderit in voluptate velit esse cillum dolorem. Duis aute irure dolor.</p>
  <a>Read More &gt;&gt;</a>
</div>

<!-- Equipment band -->
<div class="abs band" role="img" aria-label="Nurse tending a patient in a hospital bed, tinted blue"></div>
<h2 class="abs head band-title">Hire of Medical Equipments Including<br>Beds And Wheelchairs</h2>
<p class="abs band-text">We are a medical clinic for intravenous (IV) vitamin hydration and wellness therapy. A range of signature infusions and boosters are targeted at preventative health and wellness – essentially replenishing your body with the fluids and vitamins it needs to be in tip-top condition.</p>
<div class="btn btn-ghost" style="left:540px;top:2837px;width:120px">Read More</div>

<!-- Footer -->
<div class="abs brand" style="top:3118px"><span class="dot" style="width:38px;height:38px"></span><span class="name" style="font-size:38px">Lumora</span></div>
<div class="abs foot-h" style="left:471px;top:3060px">Quick Links</div>
<ul class="abs foot-list" style="left:473px;top:3096px"><li>Home</li><li>About</li><li>Products</li><li>Services</li><li>Blog</li><li>Contact</li></ul>
<div class="abs foot-h" style="left:621px;top:3060px">Links</div>
<ul class="abs foot-list" style="left:623px;top:3096px"><li>Nam libero</li><li>Cum soluta</li><li>Nobis eligendi</li><li>Optio cumque</li><li>Nihil impedit quo</li><li>Minus id quod</li></ul>
<div class="abs foot-h" style="left:785px;top:3060px">Newsletter Signup</div>
<div class="abs input">Email Address</div>
<div class="btn btn-blue" style="left:786px;top:3153px;width:105px;height:43px;font-size:15px">Read More</div>
<div class="abs rule"></div>
<p class="abs copy">Copyrights @ 2020 Lumora. All Rights Reserved.</p>

</body>
</html>
```